Business Card Design - Photographer

I am a landscape photographer and I require a business card design. 

I require two designs:
1)  a double sided business card
 and
b)  a single sided business card 

The single sided design can either be the same as the double sided (with just one side having all the information)....or it can be an entire new design. Its up to you.

My corporate colours are (CMYK):

Blue   69, 32, 0, 0
Grey  72,  64,  47,  31
Green  32,  2,  91,  0
Yellow   0, 19, 92, 0
Orange  0, 39, 75, 0

Colour space in final file should be in CMYK.

The details that need to be included on the card:

- Use the provided Logo
- Name: Wiktor Baranowski
- Email:   sales@vistalumeworks.com.au
- Website:    vistalumeworks.com.au
- Twitter:    twitter.com/vistalumeworks
- Facebook:   facebook.com/vistalumeworks
- Mobile  0417 539 662

Please use the attached template to design the logo to the specified size, including the marked bleed lines. I have also attached my logo in PNG (transparent background) and ai format for you to use.

The final file should be:
- Photoshop version with layers so I can edit the name/text etc. All non vector files should be high resolution at 1039 x 697 pixels at 300 dpi.

I also require a file as:
- Vector based PDF

Anyway questions please contact me.

Thank you

Industry/Entity Type

Landscape

Logo styles of interest
Pictorial/Combination Logo
Abstract Logo
Wordmark Logo
Lettermark Logo
Requirements
Must have
• The details that need to be included on the card:

- Use the provided Logo
- Name: Wiktor Baranowski
- Email: sales@vistalumeworks.com.au
- Website: vistalumeworks.com.au
- Twitter: twitter.com/vistalumeworks
- Facebook: facebook.com/vistalumeworks
- Mobile 0417 539 662

```html
<!DOCTYPE html>
<html lang="en">
<head>
<meta charset="utf-8">
<title>Vistalume Works – Business Cards</title>
<link href="https://fonts.googleapis.com/css2?family=Open+Sans:wght@400;600;700&display=swap" rel="stylesheet">
<style>
  :root {
    --backdrop: #343b3b;
    --card: #ffffff;
    --ink: #3b3e4c;
    --brand-grey: #3d4152;
    --brand-blue: #3d95d4;
    --text: #333333;
  }
  html, body {
    margin: 0;
    padding: 0;
    width: 987px;
    height: 1200px;
    overflow: hidden;
    background: var(--backdrop);
    font-family: "Open Sans", Arial, sans-serif;
  }
  .canvas {
    position: relative;
    width: 987px;
    height: 1200px;
  }
  .card {
    position: absolute;
    left: 92px;
    width: 790px;
    height: 450px;
    background: var(--card);
    border-radius: 26px;
    overflow: hidden;
    color: var(--text);
  }
  .card--front { top: 95px; }
  .card--back { top: 637px; width: 788px; }
  .card__swoosh {
    position: absolute;
    inset: 0;
    width: 100%;
    height: 100%;
  }
  .brand {
    position: absolute;
    left: 0;
    right: 0;
    text-align: center;
  }
  .brand__mark {
    display: block;
    margin: 0 auto;
    border-radius: 50%;
    background: var(--brand-grey);
  }
  .brand__name {
    display: block;
    font-weight: 600;
    color: var(--ink);
    letter-spacing: 0.04em;
    text-transform: uppercase;
    white-space: nowrap;
  }
  .card--front .brand { top: 58px; }
  .card--front .brand__mark { width: 96px; height: 96px; }
  .card--front .brand__name { font-size: 33px; margin-top: 66px; }
  .card--back .brand { top: 55px; }
  .card--back .brand__mark { width: 150px; height: 150px; }
  .card--back .brand__name { font-size: 50px; margin-top: 80px; }
  .holder {
    position: absolute;
    top: 277px;
    left: 0;
    right: 0;
    text-align: center;
    font-size: 18px;
  }
  .holder__name { font-size: 28px; font-weight: 700; }
  .contacts {
    position: absolute;
    top: 330px;
    left: 0;
    right: 0;
    margin: 0;
    padding: 0;
    list-style: none;
    text-align: center;
    font-size: 17.5px;
    line-height: 30px;
  }
  .contacts b { font-weight: 700; }
  .contacts .sep { margin: 0 6px; }
  .website {
    position: absolute;
    top: 396px;
    left: 0;
    right: 0;
    text-align: center;
    font-size: 25px;
    color: var(--text);
  }
</style>
</head>
<body>
<main class="canvas">
  <section class="card card--front">
    <svg class="card__swoosh" viewBox="0 0 790 450" aria-hidden="true">
      <path d="M610 0 Q740 6 790 48 L790 20 Q770 0 740 0 Z" fill="var(--brand-grey)"/>
      <path d="M660 4 Q760 20 790 62 L790 52 Q748 14 650 2 Z" fill="var(--brand-blue)"/>
      <path d="M0 410 Q90 448 170 450 L20 450 Q0 445 0 430 Z" fill="var(--brand-grey)"/>
      <path d="M0 388 Q70 428 110 438 Q50 430 0 404 Z" fill="var(--brand-blue)"/>
    </svg>
    <div class="brand">
      <span class="brand__mark"></span>
      <span class="brand__name">Vistalume Works</span>
    </div>
    <div class="holder"><span class="holder__name">Your Name</span> - Adminsitrator</div>
    <ul class="contacts">
      <li><b>m</b> : 0417 539 662</li>
      <li><b>e</b> : sales@vistalumeworks.com.au<span class="sep">|</span><b>w</b> : vistalumeworks.com.au</li>
      <li><b>t</b> : twitter.com/vistalumeworks<span class="sep">|</span><b>f</b> : facebook.com/vistalumeworks</li>
    </ul>
  </section>

  <section class="card card--back">
    <div class="brand">
      <span class="brand__mark"></span>
      <span class="brand__name">Vistalume Works</span>
    </div>
    <div class="website">www.vistalumeworks.com.au</div>
  </section>
</main>
</body>
</html>
```